Building company buisness cards

We are looking for a sharp modern new look for our business cards.
We are a New Zealand based company that specialises in house and land packages.
We have attached a photo of the current logo and would like to see if it can be improved somehow if needed.
We are open to any colours but we have chosen green at this stage.
Feel free to change the font and make the logo smarter looking.
Play with the colours and see what looks best.

We want a card that looks so good know one will want to throw it away!

Target Market(s)

Home buyers

Industry/Entity Type

Building

Contact Information for Business Card

Derek Tolvane
0217394062
dtolvane@quillmarkhomesteads.co.nz
quillmarkhomesteads.co.nz

Font styles to use
Serif
Sans Serif

Colors

Designer to choose colors to be used in the design.

Requirements
Must have
• Logo and company name on one side, details on the other side
Nice to have
• Color codes for the original green are HEX #4a8028, RGB(74,128,40), CMYK(42,0,69,50)
• Round corners, Raised and/or spot UV

```html
<!DOCTYPE html>
<html lang="en">
<head>
<meta charset="utf-8">
<title>Quillmark Homesteads – Business Card</title>
<link rel="stylesheet" href="https://fonts.googleapis.com/css2?family=Open+Sans:wght@300;400;800&family=Oswald:wght@500&display=swap">
<style>
  :root {
    --backdrop: #3a3a3a;
    --card: #262626;
    --card-edge: #1c1c1c;
    --ink-light: #e9e9e9;
    --ink-muted: #b9b9b9;
    --ink-brand: #9a9a9a;
    --green: #4a8028;
  }
  * { margin: 0; padding: 0; box-sizing: border-box; }
  html, body { width: 1200px; height: 900px; overflow: hidden; }
  body {
    background: radial-gradient(ellipse at 60% 30%, #4a4a4a 0%, var(--backdrop) 55%, #262626 100%);
    font-family: "Open Sans", sans-serif;
    position: relative;
  }
  .card {
    position: absolute;
    left: 290px;
    width: 620px;
    height: 354px;
    background: var(--card);
    border-radius: 10px;
    box-shadow: 0 18px 40px rgba(0,0,0,.45);
    overflow: hidden;
  }
  .card--front { top: 70px; }
  .card--back  { top: 476px; }

  /* front */
  .brand {
    position: absolute;
    inset: 0;
    display: flex;
    flex-direction: column;
    align-items: center;
    justify-content: center;
  }
  .brand__name {
    font-weight: 800;
    font-size: 34px;
    line-height: 1.05;
    color: var(--ink-brand);
    text-align: center;
    letter-spacing: -0.5px;
  }
  .brand__rule {
    width: 120px;
    height: 1px;
    background: #555;
    margin-top: 14px;
  }

  /* back */
  .contact {
    position: absolute;
    left: 60px;
    top: 118px;
    display: flex;
    align-items: center;
  }
  .contact__name {
    font-family: "Oswald", sans-serif;
    font-weight: 500;
    font-size: 36px;
    line-height: 1.0;
    color: var(--ink-light);
    text-align: right;
    text-transform: uppercase;
    letter-spacing: 1px;
  }
  .contact__divider {
    width: 2px;
    height: 92px;
    background: var(--ink-light);
    margin: 0 24px 0 22px;
  }
  .contact__list { list-style: none; }
  .contact__item {
    display: flex;
    align-items: center;
    font-weight: 300;
    font-size: 17px;
    color: var(--ink-muted);
    line-height: 26px;
  }
  .contact__icon { width: 14px; height: 14px; margin-right: 12px; flex: none; }
  .contact__domain { color: var(--green); }
  .card__edge {
    position: absolute;
    left: 0; right: 0; bottom: 0;
    height: 6px;
    background: var(--green);
  }
</style>
</head>
<body>
  <section class="card card--front" aria-label="Card front">
    <div class="brand">
      <p class="brand__name">quillmark<br>homesteads.</p>
      <span class="brand__rule"></span>
    </div>
  </section>

  <section class="card card--back" aria-label="Card back">
    <div class="contact">
      <p class="contact__name">Derek<br>Tolvane</p>
      <span class="contact__divider"></span>
      <ul class="contact__list">
        <li class="contact__item">
          <svg class="contact__icon" viewBox="0 0 14 14" aria-hidden="true">
            <rect x="3" y="0.5" width="8" height="13" rx="1.5" fill="none" stroke="var(--green)" stroke-width="1.6"/>
            <circle cx="7" cy="11" r="0.9" fill="var(--green)"/>
          </svg>
          0217394062
        </li>
        <li class="contact__item">
          <svg class="contact__icon" viewBox="0 0 14 14" aria-hidden="true">
            <rect x="0.5" y="2.5" width="13" height="9" rx="1" fill="var(--green)"/>
            <path d="M1 3 L7 8 L13 3" fill="none" stroke="var(--card)" stroke-width="1.2"/>
          </svg>
          dtolvane@quillmarkhomesteads.co.nz
        </li>
        <li class="contact__item">
          <svg class="contact__icon" viewBox="0 0 14 14" aria-hidden="true">
            <circle cx="7.5" cy="6" r="5" fill="none" stroke="var(--green)" stroke-width="1.6"/>
            <path d="M4 10 L1 13" stroke="var(--green)" stroke-width="1.8" stroke-linecap="round"/>
          </svg>
          <span>www.<span class="contact__domain">quillmarkhomesteads</span>.co.nz</span>
        </li>
      </ul>
    </div>
    <span class="card__edge"></span>
  </section>
</body>
</html>
```